6-seitiges Prospekt für Messer und Fräser für den industriellen Zuschnitt auf CNC-Flachbettanlagen
Zielgruppe
Hergestellt werden Messer und Fräser für den industriellen Zuschnitt auf CNC-Flachbettanlagen.
Den Einsatz dieser sieht man unter anderem hier: https://www.videoportal-beispiel.de/watch?v=QX7mLpR2aZk
Aufgabenstellung
Der Prospekt wird ein 6-Seiter (gefaltet), Seitengröße DIN A4 Hochformat und wird zweisprachig (englisch/deutsch). Er soll edel und modern anmuten.
Von euch hier soll der Titel und eine Produktseite designt werden.
Die beigestellte Datei enthält alle Beschreibungen/Texte und zu die verwendenen Bilder.

```html
<!DOCTYPE html>
<html lang="de">
<head>
<meta charset="utf-8">
<title>KlingWerk – Prospekt Messer, Fräser und Zubehör</title>
<link href="https://fonts.googleapis.com/css2?family=Open+Sans:ital,wght@0,400;0,600;0,700;1,400;1,600&display=swap" rel="stylesheet">
<style>
  :root {
    --red: #c0161c;
    --red-dark: #9c1015;
    --ink: #3a3a3a;
    --grey-light: #ececec;
    --grey-mid: #dcdcdc;
    --white: #ffffff;
    --stage: #f2f2f2;
    --gold: #f2c200;
    --black: #111111;
  }
  * { box-sizing: border-box; margin: 0; padding: 0; }
  html, body { width: 1200px; height: 1072px; overflow: hidden; }
  body {
    background: var(--stage);
    font-family: "Open Sans", Arial, sans-serif;
    color: var(--ink);
  }
  .brochure {
    position: absolute; left: 45px; top: 56px;
    width: 1110px; height: 960px;
    display: flex;
    box-shadow: 0 6px 24px rgba(0,0,0,.12);
  }
  .panel { position: relative; width: 370px; height: 960px; overflow: hidden; background: var(--white); }
  .panel + .panel { border-left: 1px solid var(--grey-mid); }

  /* panel 1 – product page */
  .welcome-head { position: absolute; left: 0; top: 0; width: 100%; height: 130px; padding: 40px 30px; }
  .welcome-head h2 { color: var(--red); font-size: 19px; font-weight: 700; }
  .welcome-head p { color: var(--red); font-size: 17px; font-style: italic; }
  .intro { position: absolute; left: 0; top: 130px; width: 100%; height: 200px; background: var(--red); color: var(--white); padding: 30px; font-size: 11.5px; line-height: 1.55; }
  .intro p + p { margin-top: 14px; }
  .intro .en { font-style: italic; }
  .products { position: absolute; left: 0; top: 330px; width: 100%; height: 550px; background: var(--grey-light); padding: 20px; }
  .section-title { background: var(--white); padding: 18px 20px; margin-bottom: 18px; }
  .section-title h3 { color: var(--red); font-size: 20px; font-weight: 700; }
  .section-title p { color: var(--red); font-size: 16px; font-style: italic; padding-left: 22px; }
  .product { background: var(--white); padding: 14px 20px; height: 200px; margin-bottom: 10px; position: relative; }
  .product h4 { font-size: 14px; font-weight: 700; color: var(--ink); }
  .product .spec { font-size: 8.5px; line-height: 1.5; color: #666; margin-top: 6px; }
  .product .spec + .spec { margin-top: 8px; }
  .product-photo { position: absolute; left: 20px; right: 20px; bottom: 14px; height: 56px; background: linear-gradient(100deg, #f7f7f7 0%, #b9b9b9 45%, #e2e2e2 70%, #f7f7f7 100%); }
  .footer { position: absolute; left: 0; top: 880px; width: 100%; height: 80px; background: var(--grey-mid); padding: 30px; font-size: 15px; font-weight: 700; color: var(--red); }

  /* panel 2 – contact */
  .contact-top { position: absolute; left: 0; top: 0; width: 100%; height: 130px; background: var(--grey-light); }
  .contact-field { position: absolute; left: 0; top: 130px; width: 100%; height: 750px; background: var(--red); }
  .contact-box { position: absolute; left: 22px; right: 22px; top: 30px; background: var(--white); padding: 22px; font-size: 10px; line-height: 1.6; color: var(--red-dark); }
  .contact-box strong { font-weight: 700; }
  .contact-box p + p { margin-top: 12px; }
  .hotline { color: var(--red); }
  .hotline strong { font-weight: 700; }

  /* panel 3 – cover */
  .brand { position: absolute; right: 28px; top: 42px; display: flex; align-items: center; gap: 8px; }
  .brand-square { width: 26px; height: 26px; background: var(--red); }
  .brand-name { font-size: 26px; font-weight: 700; color: var(--red); }
  .cover-photo { position: absolute; left: 0; width: 100%; background: linear-gradient(135deg, #f4f4f4 0%, #c9c9c9 40%, #8d8d8d 60%, #e8e8e8 100%); }
  .cover-photo.top { top: 140px; height: 420px; }
  .cover-photo.bottom { top: 720px; height: 160px; background: linear-gradient(160deg, #d8d8d8 0%, #9a9a9a 50%, #e6e6e6 100%); }
  .cover-band { position: absolute; left: 0; top: 520px; width: 100%; height: 230px; }
  .cover-title { position: absolute; left: 30px; top: 590px; color: var(--white); }
  .cover-title h1 { font-size: 22px; font-weight: 700; line-height: 1.2; }
  .cover-title p { font-size: 17px; font-style: italic; margin-top: 4px; }
  .cover-foot { position: absolute; left: 0; top: 880px; width: 100%; height: 80px; background: var(--white); padding: 22px 30px; }
  .flag-stripes { display: flex; width: 100px; height: 4px; }
  .flag-stripes span { flex: 1; }
  .flag-stripes .s1 { background: var(--black); }
  .flag-stripes .s2 { background: var(--red); }
  .flag-stripes .s3 { background: var(--gold); }
  .made-in { font-size: 10px; color: #777; margin-top: 6px; }
</style>
</head>
<body>
<main class="brochure">

  <section class="panel product-page">
    <header class="welcome-head">
      <h2>Begrüssungstext</h2>
      <p>entsprechende Übersetzung</p>
    </header>
    <div class="intro">
      <p>Begrüssungstext dies ist Platzhaltertext. Hier können einige ergänzende Worte stehen.</p>
      <p>maximal 540 Zeichen inkl Übersetzung</p>
      <p class="en">This is a placeholder for the introduction. Here is space for a maximum of 540 letters including the translation.</p>
    </div>
    <div class="products">
      <div class="section-title">
        <h3>1. single edge blades</h3>
        <p>Einschneidige Messer</p>
      </div>
      <article class="product">
        <h4>KW-110</h4>
        <p class="spec">alternative for Cutron CT-7A / PL-3381 Plottaro<br>Ersatz für Cutron CT-7A / PL-3381 Plottaro</p>
        <p class="spec">Max. Schnitthöhe: 2,8 mm | Schaftbreite: 5,5 mm<br>Länge: 28 mm | Schneidwinkel: 35°</p>
        <div class="product-photo" role="img" aria-label="Produktfoto einschneidiges Messer KW-110"></div>
      </article>
      <article class="product">
        <h4>KW-140</h4>
        <p class="spec">alternative for Cutron CT-9B / PL-5520 Plottaro PK-LX20<br>Ersatz für Cutron CT-9B / PL-5520 Plottaro PK-LX20</p>
        <p class="spec">Max. Schnitthöhe: 20 mm | Schaftbreite: 6 mm<br>Länge: 50 mm</p>
        <div class="product-photo" role="img" aria-label="Produktfoto einschneidiges Messer KW-140"></div>
      </article>
    </div>
    <footer class="footer">e-mail: info@klingwerk-beispiel.de</footer>
  </section>

  <section class="panel contact-page">
    <div class="contact-top"></div>
    <div class="contact-field">
      <address class="contact-box">
        <p><strong>KlingWerk GmbH</strong><br>Musterweg 12<br>86000 Beispielstadt<br>Deutschland</p>
        <p>Telefon: +49 (0)123 45 678 900<br>Telefax: +49 (0)123 45 678 901</p>
        <p>Unsere Telefon-Hotline ist<br>Montag bis Freitag von<br>8:00 Uhr bis 16:00 Uhr für Sie da.</p>
        <p>Telefon: +49 (0)123 45 678 900<br>E-Mail: info@klingwerk-beispiel.de</p>
      </address>
    </div>
    <footer class="footer hotline"><strong>service hotline</strong> +49 (0)123 - 45 678 900</footer>
  </section>

  <section class="panel cover">
    <div class="brand">
      <span class="brand-square"></span>
      <span class="brand-name">KlingWerk</span>
    </div>
    <div class="cover-photo top" role="img" aria-label="Fotocollage von Messerklingen und Fräsern"></div>
    <div class="cover-photo bottom" role="img" aria-label="Foto eines Kreismessers"></div>
    <svg class="cover-band" viewBox="0 0 370 230" preserveAspectRatio="none" aria-hidden="true">
      <polygon points="0,40 370,0 370,170 0,230" fill="var(--red)"/>
    </svg>
    <div class="cover-title">
      <h1>blades, router bits &amp;<br>accessories</h1>
      <p>Messer, Fräser und Zubehör</p>
    </div>
    <footer class="cover-foot">
      <div class="flag-stripes"><span class="s1"></span><span class="s2"></span><span class="s3"></span></div>
      <p class="made-in">made in Germany</p>
    </footer>
  </section>

</main>
</body>
</html>
```